Community Harvest Festival Poster

Seeking a poster design to advertise our community’s annual Harvest Festival. We will utilize and display printed posters as well as distribute PDFs via our weekly e-news letters. This years "theme" is, "Copper Kettle/Maple Lane Meadow, Where City and Country Meet." The vibe is a bohemian, beatnik, street scene, meets a old fashioned orchard.

Target Market(s)

NYC School Community- should appeal to an audience that ranges from kids to grandparents. Very family oriented, with wide appeal, and must be eye catching.

Other font styles liked:
• One style should be more of a "Country" font, the other should have more of a clean city vibe.

Colors
acd037
ffc214
f68e4e
eaf2ce

Requirements
Must have
• The following copy:
• Copper Kettle Maple Lane Meadow
• Where City and Country Meet
• Celebrate C&C With Great Food, Music, Entertainment, And Fun!
• Saturday, October 19th 2019
• 12:00-4:00pm
• Tickets will be available for sale at Drop off and Pick up
Nice to have
• I'm not limited, but a couple of ideas that could be cool:
• One incorporated the background of a street, i.e. pavement, which has leaves blowing over it, and perhaps an apple or two rolling onto the page.
• Another has a diagonal breakup of the image, with one side pavement and the other side rustic wood, also with leaves sweeping across.
• I've also attached images of previous festival posters that I have gravitated to for some idea of quality I'm looking for.
Should not have
• Anything inappropriate for children.

```html
<!DOCTYPE html>
<html lang="en">
<head>
<meta charset="utf-8">
<title>Harvest Festival – Copper Kettle Maple Lane Meadow</title>
<link rel="stylesheet" href="https://fonts.googleapis.com/css2?family=Lobster&family=Smokum&family=Oswald:wght@400;500&display=swap">
<style>
  :root {
    --wood-light: #f1f1f1;
    --wood-mid: #d9d9d9;
    --ink: #2b2b2b;
    --green: #acd037;
    --orange: #f68e4e;
    --shadow-brown: #4a2416;
    --pumpkin: #e0621f;
    --pumpkin-deep: #c9471a;
    --squash: #f2a91e;
    --cabbage: #d6e6b6;
    --apple: #d9643a;
    --wheat: #e9b26c;
    --corn: #f3c92c;
    --leaf: #5da833;
    --white: #ffffff;
  }
  html, body {
    margin: 0;
    padding: 0;
    overflow: hidden;
    background: #ffffff;
  }
  .poster {
    position: relative;
    width: 1200px;
    height: 1200px;
    overflow: hidden;
    background: linear-gradient(180deg, var(--wood-light) 0%, #e6e6e6 55%, var(--wood-mid) 100%);
  }
  .backdrop {
    position: absolute;
    inset: 0;
    background: linear-gradient(90deg, #ececec, #f4f4f4 50%, #e2e2e2);
  }
  .produce {
    position: absolute;
    border-radius: 50%;
  }
  .produce--pumpkin { background: radial-gradient(circle at 45% 40%, var(--pumpkin), var(--pumpkin-deep)); }
  .produce--squash { background: var(--squash); border-radius: 45% 45% 50% 50% / 35% 35% 60% 60%; }
  .produce--cabbage { background: var(--cabbage); }
  .produce--apple { background: radial-gradient(circle at 40% 40%, #f0a24a, var(--apple)); }
  .produce--corn { background: var(--corn); border-radius: 40%; }
  .produce--wheat { background: linear-gradient(90deg, rgba(233,178,108,0), var(--wheat)); border-radius: 40%; }
  .produce--greens { background: var(--leaf); border-radius: 50% 50% 40% 40%; }

  .title {
    position: absolute;
    left: 130px;
    top: 150px;
    width: 940px;
    margin: 0;
    font-family: "Lobster", cursive;
    font-weight: 400;
    font-size: 128px;
    line-height: 1;
    white-space: nowrap;
    transform: rotate(-3deg);
    transform-origin: left center;
    z-index: 3;
  }
  .title__word--harvest { color: var(--green); text-shadow: 6px 5px 0 var(--shadow-brown); }
  .title__word--festival { color: var(--orange); text-shadow: 6px 5px 0 var(--shadow-brown); }

  .rule {
    position: absolute;
    left: 466px;
    top: 392px;
    width: 276px;
    height: 3px;
    background: #3a3a3a;
    z-index: 3;
  }
  .theme {
    position: absolute;
    left: 200px;
    top: 448px;
    width: 800px;
    margin: 0;
    text-align: center;
    white-space: nowrap;
    font-family: "Smokum", serif;
    font-weight: 400;
    font-size: 72px;
    line-height: 84px;
    letter-spacing: 3px;
    color: var(--ink);
    z-index: 3;
  }
  .notes {
    position: absolute;
    left: 101px;
    top: 712px;
    margin: 0;
    font-family: "Oswald", sans-serif;
    font-weight: 400;
    font-size: 17px;
    line-height: 28px;
    letter-spacing: 2px;
    color: var(--ink);
    text-transform: uppercase;
    white-space: nowrap;
    z-index: 3;
  }
  .notes p { margin: 0 0 28px; }
  .date-badge {
    position: absolute;
    left: 513px;
    top: 835px;
    width: 156px;
    height: 156px;
    border-radius: 50%;
    background: var(--green);
    z-index: 3;
    display: flex;
    flex-direction: column;
    align-items: center;
    justify-content: center;
    font-family: "Oswald", sans-serif;
    color: var(--white);
    text-align: center;
    text-transform: uppercase;
  }
  .date-badge::before {
    content: "";
    position: absolute;
    inset: 5px;
    border: 1px solid var(--white);
    border-radius: 50%;
  }
  .date-badge__line { font-size: 20px; font-weight: 500; line-height: 22px; letter-spacing: 1px; }
  .date-badge__time { font-size: 12px; line-height: 18px; letter-spacing: 1px; margin-top: 2px; }
  .tickets {
    position: absolute;
    right: 104px;
    top: 878px;
    margin: 0;
    text-align: right;
    font-family: "Oswald", sans-serif;
    font-size: 17px;
    line-height: 28px;
    letter-spacing: 2px;
    color: var(--ink);
    text-transform: uppercase;
    white-space: nowrap;
    z-index: 3;
  }
</style>
</head>
<body>
<div class="poster">
  <div class="backdrop" role="img" aria-label="Whitewashed rustic wooden planks"></div>

  <div class="produce produce--cabbage" role="img" aria-label="Cabbage" style="left:242px;top:-56px;width:236px;height:236px;"></div>
  <div class="produce produce--pumpkin" role="img" aria-label="Orange pumpkin" style="left:-25px;top:18px;width:336px;height:336px;"></div>
  <div class="produce produce--corn" role="img" aria-label="Ear of corn" style="left:850px;top:120px;width:110px;height:34px;transform:rotate(35deg);"></div>
  <div class="produce produce--pumpkin" role="img" aria-label="Orange pumpkin" style="left:888px;top:-43px;width:186px;height:186px;"></div>
  <div class="produce produce--pumpkin" role="img" aria-label="Orange pumpkin" style="left:1000px;top:-56px;width:236px;height:236px;"></div>
  <div class="produce produce--squash" role="img" aria-label="Butternut squash" style="left:963px;top:62px;width:155px;height:298px;"></div>
  <div class="produce produce--pumpkin" role="img" aria-label="Orange pumpkin" style="left:1060px;top:149px;width:224px;height:224px;"></div>
  <div class="produce produce--squash" role="img" aria-label="Halved butternut squash" style="left:1097px;top:379px;width:120px;height:186px;"></div>
  <div class="produce produce--wheat" role="img" aria-label="Wheat ears" style="left:1100px;top:620px;width:130px;height:60px;transform:rotate(-40deg);"></div>
  <div class="produce produce--apple" role="img" aria-label="Red apple" style="left:57px;top:429px;width:110px;height:110px;"></div>
  <div class="produce produce--wheat" role="img" aria-label="Wheat ears" style="left:-30px;top:740px;width:120px;height:60px;transform:rotate(-35deg);"></div>
  <div class="produce produce--pumpkin" role="img" aria-label="Orange pumpkin" style="left:-87px;top:820px;width:248px;height:248px;"></div>
  <div class="produce produce--pumpkin" role="img" aria-label="Orange pumpkin" style="left:-31px;top:919px;width:348px;height:348px;"></div>
  <div class="produce produce--squash" role="img" aria-label="Halved butternut squash" style="left:292px;top:970px;width:192px;height:240px;"></div>
  <div class="produce produce--corn" role="img" aria-label="Ear of corn" style="left:505px;top:1105px;width:44px;height:120px;transform:rotate(15deg);"></div>
  <div class="produce produce--greens" role="img" aria-label="Bok choy" style="left:1030px;top:910px;width:120px;height:190px;"></div>
  <div class="produce produce--apple" role="img" aria-label="Red apple" style="left:969px;top:1112px;width:86px;height:86px;"></div>

  <h1 class="title"><span class="title__word--harvest">Harvest</span> <span class="title__word--festival">Festival</span></h1>

  <div class="rule"></div>

  <h2 class="theme">COPPER KETTLE<br>MAPLE LANE MEADOW<br>WHERE CITY AND<br>COUNTRY MEET</h2>

  <div class="notes">
    <p>Upmarket<br>Requirements<br>Must have</p>
    <p>The following copy:<br>Copper Kettle Maple Lane Meadow<br>Where city and country meet<br>Celebrate C&amp;C with great food,<br>music, entertainment, and fun!</p>
  </div>

  <div class="date-badge">
    <span class="date-badge__line">Saturday</span>
    <span class="date-badge__line">October 19th</span>
    <span class="date-badge__line">2019</span>
    <span class="date-badge__time">12:00–4:00pm</span>
  </div>

  <p class="tickets">Tickets will be available for sale<br>at drop off and pick up<br>Nice to have</p>
</div>
</body>
</html>
```